Design Project - Finance Website (Only need PSD)

UPDATED PROJECT (Now only PSD needed)
Need a Wordpress design for a company called "Corvale Lending Partners". The company provides finance for corporate clients, businesses and property developers. The design should be business like with appealing colours that communicate trust. I have uploaded a banner and logo to be incorporated or feel free to design something better if you think you can.
** I now only need the PSD
** I want something that is actually designed rather than from a template.
Thanks
Updates
The website will be used for lead generation so the contact form with adjustable fields in the Wordpress backend should be fairly prominent on the page.
I have uploaded a banner and logo for the site. None of the designs I have seen so far were good enough so the first decent design using the new banner and logo provided will win the job. I do not want just a template that has been cut and paste from somewhere else, I want decent design. If anyone provides a decent design then I will give an extra bonus of $150.
Reason: I have uploaded a banner and logo for the site. None of the designs I have seen so far were good enough so the first decent design using the new banner and logo provided will win the job. I do not want just a template that has been cut and paste from somewhere else, I want decent design. If anyone provides a decent design then I will give an extra bonus of $150.
Thanks
Target Market(s)
Business owners & property developers
Industry/Entity Type
Finance
Requirements
Must have
- Contact form on home page that can be altered through the back end eg. ability to add or remove fields. Widgetised sidebars.
Nice to have
- Widgetised footer.

```html
<!DOCTYPE html>
<html lang="en">
<head>
<meta charset="utf-8">
<title>Corvale Lending Partners</title>
<link rel="stylesheet" href="https://fonts.googleapis.com/css2?family=Open+Sans:ital,wght@0,400;0,600;1,400&family=PT+Sans:wght@400;700&display=swap">
<style>
:root{
  --green:#8cbf3f;
  --green-dark:#6f9e22;
  --green-line:#c6dd9c;
  --lime:#a8d62b;
  --ink:#2b2b2b;
  --text:#555;
  --muted:#888;
  --rule:#e1e1e1;
  --panel:#f3f3f3;
  --footer:#0d0d0d;
  --footer-base:#2c2c2c;
  --white:#fff;
}
*{box-sizing:border-box;margin:0;padding:0}
html,body{width:996px;height:1200px;overflow:hidden;background:var(--white)}
body{position:relative;font-family:"Open Sans",Arial,sans-serif;color:var(--text);font-size:10.5px;line-height:1.5}
.abs{position:absolute}
.top-strip{left:0;top:0;width:996px;height:8px;background:#dcdcdc}
.social{top:28px;width:29px;height:29px;border-radius:50%;background:linear-gradient(#fff,#e6e6e6);border:1px solid #d3d3d3;box-shadow:0 1px 2px rgba(0,0,0,.15)}
.social.one{left:670px}.social.two{left:704px}
.search{left:746px;top:29px;width:222px;height:27px;border:1px solid #dcdcdc;border-radius:3px;background:linear-gradient(#fff,#f2f2f2);font-style:italic;color:#999;font-size:11px;padding:6px 9px}
.search svg{position:absolute;right:7px;top:5px}
.brand{left:26px;top:78px;font-size:23px;color:var(--ink);letter-spacing:.1px}
.nav{left:376px;top:84px;width:592px;height:43px;border:1px solid #ddd;border-radius:3px;display:flex;align-items:center;justify-content:space-around;font-size:13.5px;color:#444;background:#fff}
.nav span+span{border-left:1px solid #ddd;padding-left:22px}
.banner{left:18px;top:132px;width:952px;height:285px;background:linear-gradient(180deg,#8fb5d8 0%,#b7cfe3 40%,#6e8a6f 75%,#7a5a3c 100%)}
.banner-shadow{left:40px;top:417px;width:900px;height:8px;background:radial-gradient(ellipse at top,rgba(0,0,0,.25),transparent 70%)}
.steps{left:565px;top:242px;width:341px;height:114px;background:#fff;border-radius:5px;padding:8px 16px}
.steps li{list-style:none;display:flex;align-items:center;height:32px;font-size:14px;color:#333;border-bottom:1px solid #e6e6e6}
.steps li:last-child{border:none}
.steps b{width:23px;height:23px;border-radius:50%;background:#000;color:#fff;font-size:13px;display:flex;align-items:center;justify-content:center;margin-right:12px;font-weight:600}
.heading{font-family:"PT Sans",Arial,sans-serif;color:var(--green-dark);font-size:18px;border-bottom:1px solid var(--green-line);padding-bottom:3px}
.welcome-h{left:17px;top:438px;width:627px}
.welcome-text{left:17px;top:473px;width:630px}
.welcome-text p{margin-bottom:7px}
.btn{background:var(--green);color:#fff;border:1px solid #7aa92f;border-radius:4px;font-size:12.5px;text-align:center}
.read-more{left:16px;top:613px;width:86px;height:26px;line-height:24px}
.testi-h{left:667px;top:438px;width:309px}
.testi{left:669px;top:473px;width:307px;height:136px;background:var(--panel);padding:14px 18px;font-style:italic;font-size:10.5px;color:#666}
.testi p{margin-bottom:5px}
.author{right:24px;top:621px;font-style:italic;font-size:12px;color:#444}
.card{top:660px;height:303px;border:1px solid #e2e2e2;border-radius:4px;background:#fff;box-shadow:0 2px 3px rgba(0,0,0,.06)}
.card-head{height:37px;background:var(--green);border-radius:4px 4px 0 0;color:#fff;font-family:"PT Sans",Arial,sans-serif;font-weight:700;font-size:16px;letter-spacing:.5px;padding:8px 13px;position:relative}
.news{left:12px;width:308px}.case{left:338px;width:308px}.contact{left:667px;width:308px}
.news-item{position:absolute;left:12px;width:285px}
.thumb{position:absolute;left:0;top:0;width:79px;height:68px;border:1px solid #ccc}
.item-body{position:absolute;left:91px;top:0;width:200px;font-size:10.5px}
.item-body h3{font-size:13px;font-weight:600;color:#333;line-height:1.3}
.case-thumb{left:13px;top:51px;width:96px;height:82px;border:1px solid #ccc;background:linear-gradient(160deg,#8fb0d6,#d7dfe6 55%,#a59a84)}
.case-body{position:absolute;left:120px;top:51px;width:180px}
.case-body h3{font-size:13px;font-weight:600;color:#333;line-height:1.3}
.case-more{position:absolute;left:13px;top:152px;width:290px}
.case-more p{margin-bottom:7px}
.outline-btn{position:absolute;right:14px;bottom:14px;border:1px solid #ccc;border-radius:3px;color:var(--green-dark);padding:3px 9px;font-size:12px}
.field{position:absolute;left:14px;width:292px;height:31px;border:1px solid #e0e0e0;border-radius:4px;background:linear-gradient(#fafafa,#f0f0f0);font-style:italic;color:#999;font-size:11px;padding:7px 11px}
.check{position:absolute;left:18px;top:191px;font-size:11.5px;color:#777;display:flex;align-items:center}
.check i{width:18px;height:18px;border:1px solid #ccc;border-radius:2px;margin-right:8px;background:#fff}
.submit{position:absolute;left:195px;top:236px;width:97px;height:26px;line-height:24px}
.footer{left:0;top:982px;width:996px;height:174px;background:radial-gradient(ellipse at 50% 0,#3a3a3a,var(--footer) 55%)}
.foot-col{position:absolute;top:24px;width:130px}
.foot-col li{list-style:none;color:var(--lime);font-size:12px;height:24px;line-height:23px;border-bottom:1px solid #2d2d2d;padding-left:12px;position:relative}
.foot-col li:last-child{border:none}
.foot-col li::before{content:"";position:absolute;left:2px;top:9px;border-left:4px solid var(--lime);border-top:3px solid transparent;border-bottom:3px solid transparent}
.foot-brand{right:26px;top:46px;color:#9a9a9a;font-size:20px}
.footer-base{left:0;top:1156px;width:996px;height:44px;background:var(--footer-base);color:var(--lime);font-size:11px;text-align:right;padding:13px 22px}
</style>
</head>
<body>
<div class="abs top-strip"></div>
<div class="abs social one"></div>
<div class="abs social two"></div>
<div class="abs search">Search here
  <svg width="18" height="18" viewBox="0 0 18 18"><circle cx="7" cy="7" r="5" fill="none" stroke="#999" stroke-width="2"/><line x1="11" y1="11" x2="16" y2="16" stroke="#999" stroke-width="3"/></svg>
</div>
<div class="abs brand">Corvale Lending Partners</div>
<nav class="abs nav"><span>Home</span><span>About us</span><span>Services</span><span>Finance</span><span>Real Estate</span><span>Contact us</span></nav>

<div class="abs banner" role="img" aria-label="Photo of a modern glass office building with trees in front"></div>
<div class="abs banner-shadow"></div>
<ol class="abs steps">
  <li><b>1</b>Compare several capital provider rates</li>
  <li><b>2</b>Access to real estate and hedge funds</li>
  <li><b>3</b>Optimise your capital returns</li>
</ol>

<h2 class="abs heading welcome-h">WELCOME TO CORVALE LENDING PARTNERS</h2>
<div class="abs welcome-text">
  <p>Brightwell Studio is a web service company, offering a wide range of services which range from designing and development, that is covering almost all the fields in the best possible way. To be the best we know what and how to present beautifully the working of the client's need and their advantages be highlighted. We act in accordance with the Industry certified processes to deliver the best to our clients all over the world. Over years we have built a strong reputation in providing website design and web development services.</p>
  <p>Thus, Wanna get ahead in the competition with other websites…. Brightwell Studio provide you with an attractive and most convincing website to enhance your marketing goals.The only way to success is through the right path and that's what we provide you. None of the other companies has the result we do.</p>
</div>
<div class="abs btn read-more">Read more</div>

<h2 class="abs heading testi-h">TESTIMONIALS</h2>
<div class="abs testi">
  <p>Brightwell Studio think graphic design as a combination and collaboration of ideas and technology.</p>
  <p>Our Website Design team give an unforgettable impression on the customers and the clients. We can assure you that this is the best place for requirement of yours regarding website design solutions</p>
</div>
<div class="abs author">BY AUTHOR NAME</div>

<section class="abs card news">
  <div class="card-head">LATEST NEWS
    <svg style="position:absolute;right:13px;top:13px" width="22" height="11" viewBox="0 0 22 11"><path d="M8 0v11L0 5.5z" fill="#fff"/><path d="M14 0v11l8-5.5z" fill="#fff"/></svg>
  </div>
  <div class="news-item" style="top:50px">
    <div class="thumb" role="img" aria-label="Photo of a residential tower" style="background:linear-gradient(#9cc0e4,#dfe6ec 60%,#7d9a6c)"></div>
    <div class="item-body"><h3>Headline goes here</h3>Brightwell Studio is a web service company, offering a wide range of services which range from designing</div>
  </div>
  <div class="news-item" style="top:135px">
    <div class="thumb" role="img" aria-label="Photo of a brick office block" style="background:linear-gradient(#6f97c9,#a46a45 50%,#7b4c30)"></div>
    <div class="item-body"><h3>Headline goes here</h3>Brightwell Studio is a web service company, offering a wide range of services which range from designing</div>
  </div>
  <div class="news-item" style="top:220px">
    <div class="thumb" role="img" aria-label="Photo of a curved glass skyscraper" style="background:linear-gradient(150deg,#e4eef6,#7fa3c4 60%,#3c5d80)"></div>
    <div class="item-body"><h3>Headline goes here</h3>Brightwell Studio is a web service company, offering a wide range of services which range from designing</div>
  </div>
</section>

<section class="abs card case">
  <div class="card-head">CASE STUDY</div>
  <div class="abs case-thumb" role="img" aria-label="Photo of a modern commercial building entrance"></div>
  <div class="case-body"><h3>Headline goes here</h3>Brightwell Studio is a web service company, offering a wide range of services which range from designing and development.</div>
  <div class="case-more">
    <p>We act in accordance with the Industry certified processes to deliver the best to our clients all over the world.</p>
    <p>So stick to the best that's how you will be the best don't opt for the second best. Our expertise does not limit itself to web development but also it includes Web Hosting, Search Engine Optimization, E-Commerce. We partner hundreds of organization to enhance.</p>
  </div>
  <div class="outline-btn">READ MORE</div>
</section>

<section class="abs card contact">
  <div class="card-head">QUICK CONTACT</div>
  <div class="field" style="top:53px">type your name</div>
  <div class="field" style="top:103px">type your email address</div>
  <div class="field" style="top:152px">type your phone</div>
  <div class="check"><i></i>Subscribe to our Newsletters</div>
  <div class="btn submit">Submit Now</div>
</section>

<footer class="abs footer">
  <ul class="foot-col" style="left:31px"><li>About Us</li><li>Contact Us</li><li>Services</li><li>Lorem Ipsum</li><li>Other Links</li></ul>
  <ul class="foot-col" style="left:167px"><li>About Us</li><li>Contact Us</li><li>Services</li><li>Lorem Ipsum</li><li>Other Links</li></ul>
  <ul class="foot-col" style="left:307px"><li>About Us</li><li>Contact Us</li><li>Services</li><li>Lorem Ipsum</li><li>Other Links</li></ul>
  <div class="abs foot-brand">Corvale Lending Partners</div>
</footer>
<div class="abs footer-base">© 2012 Company Name &nbsp;|&nbsp; All right reserved</div>
</body>
</html>
```